New business card/stationary for a consulting company

I am looking for a clean and very professional looking business card for my consulting company as well as corresponding stationary. I am uploading our logo. I like simple and powerful for the feel. No graphics but I am open on everything else. Below is my contact information but would like the final to be in a version I can add my employees information into and print. Thank you.

Daniel Whitcombe
dan@ferncliffadvisory.com
2870 North 9th Avenue, Summit Floor, Elm Ridge, Illinois 60531
www.ferncliffadvisory.com

Industry/Entity Type

Consulting

Contact Information for Business Card

Daniel Whitcombe
dan@ferncliffadvisory.com
www.ferncliffadvisory.com

Font styles to use
Serif
Sans Serif

Requirements
Must have
• Our logo and the business card details.
Nice to have
• our website www.ferncliffadvisory.com

```html
<!DOCTYPE html>
<html lang="en">
<head>
<meta charset="utf-8">
<title>Ferncliff Advisory – Business Card</title>
<link href="https://fonts.googleapis.com/css2?family=Open+Sans:wght@300;400;700&display=swap" rel="stylesheet">
<style>
  :root {
    --navy: #0c0f7c;
    --paper: #f7f7f6;
    --ink: #55575c;
    --rule: #c9c9cc;
    --stage: #e4e4e6;
    --white: #ffffff;
  }
  * { box-sizing: border-box; margin: 0; padding: 0; }
  html, body {
    width: 1200px; height: 900px; overflow: hidden;
    background: var(--stage);
    font-family: "Open Sans", Arial, sans-serif;
  }
  .card {
    position: absolute;
    left: 320px;
    width: 560px; height: 320px;
    box-shadow: 0 6px 18px rgba(0,0,0,0.18);
  }
  .card__frame {
    position: absolute; inset: 14px;
    border: 2px solid;
  }
  .card--back { top: 100px; background: var(--navy); }
  .card--back .card__frame { border-color: var(--white); }
  .card--front { top: 470px; background: var(--paper); }
  .card--front .card__frame { border-color: var(--navy); }

  .brand {
    position: absolute;
    display: flex; align-items: center; gap: 12px;
    font-weight: 300; letter-spacing: 1.5px; text-transform: uppercase;
    white-space: nowrap;
  }
  .brand__mark { display: block; width: 18px; height: 18px; }
  .card--back .brand {
    left: 50%; top: 50%; transform: translate(-50%, -50%);
    color: var(--white); font-size: 24px;
  }
  .card--back .brand__mark { background: var(--white); }
  .card--front .brand {
    left: 40px; top: 152px;
    color: var(--navy); font-size: 18px;
  }
  .card--front .brand__mark { background: var(--navy); width: 14px; height: 14px; }

  .divider {
    position: absolute; left: 292px; top: 60px; width: 1px; height: 200px;
    background: linear-gradient(var(--paper), var(--rule) 30%, var(--rule) 70%, var(--paper));
  }
  .contact {
    position: absolute; left: 312px; top: 70px;
    color: var(--ink); font-size: 13px; line-height: 1.45;
  }
  .contact__name {
    color: var(--navy); font-weight: 700; font-size: 16px;
    text-transform: uppercase; letter-spacing: 0.3px; margin-bottom: 12px;
  }
  .contact__address { margin-bottom: 8px; }
  .contact__line { display: flex; align-items: center; gap: 8px; }
  .contact__icon { width: 11px; height: 11px; flex: none; }
</style>
</head>
<body>
  <section class="card card--back" aria-label="Business card, back">
    <div class="card__frame"></div>
    <div class="brand"><span class="brand__mark"></span>Ferncliff Advisory</div>
  </section>

  <section class="card card--front" aria-label="Business card, front">
    <div class="card__frame"></div>
    <div class="brand"><span class="brand__mark"></span>Ferncliff Advisory</div>
    <div class="divider"></div>
    <div class="contact">
      <p class="contact__name">Daniel Whitcombe</p>
      <p class="contact__address">2870 North 9th Avenue<br>Summit Floor, Elm Ridge<br>Illinois 60531</p>
      <p class="contact__line">
        <svg class="contact__icon" viewBox="0 0 12 12"><rect x="0.5" y="2" width="11" height="8" fill="var(--navy)"/><path d="M0.5 2 L6 6.5 L11.5 2" stroke="var(--paper)" stroke-width="1" fill="none"/></svg>
        dan@ferncliffadvisory.com
      </p>
      <p class="contact__line">
        <svg class="contact__icon" viewBox="0 0 12 12"><circle cx="6" cy="6" r="5.5" fill="var(--navy)"/><path d="M0.5 6 H11.5 M6 0.5 C3 3.5 3 8.5 6 11.5 M6 0.5 C9 3.5 9 8.5 6 11.5" stroke="var(--paper)" stroke-width="0.9" fill="none"/></svg>
        www.ferncliffadvisory.com
      </p>
    </div>
  </section>
</body>
</html>
```